Alaska Law Firm Needs a Sticker Design

We need a design for stickers to put on already-printed brochures. We mail the brochures to potential clients so they can learn more about accident-induced injuries, insurance claims, legal representation, and our own law firm.

One of our lawyers wrote a book that provides a helpful overview of personal injury claims. We are offering this book for free to anyone who calls and requests it. Therefore, the sticker design should include one of the following phrases, or something very similar:
a) "Still have questions? Call and request our book-- for free!"
b) "Still have questions about auto accident claims? Call and request our book today."
c) "Still have questions about filing a claim? Call and request a free copy of our book."
d) "Still have questions? Call us today to request a free copy of our book, Clear Lanes Ahead."
e) "To learn more about automobile accidents and insurance, call today and request a free copy of our book."

The sticker should be approximately 3"x3" and may be a circle, square, rectangle, or ellipsis. The sticker will be placed on the back of the folder, which is light blue. We would like the sticker to match the color scheme of our website and the folder.

I will upload an image of the book cover as soon as I obtain it.

Law Firm

Font styles to use
Serif
Sans Serif

Requirements
Should not have
• Bright colors that aren't already used in the folder design. e.g. no bright orange, pink, chartreuse, turquoise, yellow, red.

```html
<!DOCTYPE html>
<html lang="en">
<head>
<meta charset="utf-8">
<title>Still Have Questions – Free Book Sticker</title>
<link href="https://fonts.googleapis.com/css2?family=Ubuntu:wght@500;700&family=Gabriela&family=Merienda:wght@700&display=swap" rel="stylesheet">
<style>
  :root {
    --backdrop-light: #f7f7f7;
    --backdrop-mid: #d9d9d9;
    --sticker-white: #ffffff;
    --gloss-grey: #ececec;
    --navy: #1b2670;
    --navy-bright: #1f3196;
    --ink-dark: #262626;
    --ink-script: #2a2a2a;
  }
  html, body {
    margin: 0;
    padding: 0;
    overflow: hidden;
  }
  body {
    width: 1200px;
    height: 1200px;
    background: radial-gradient(ellipse at 50% 50%, var(--backdrop-light) 0%, var(--backdrop-light) 45%, var(--backdrop-mid) 100%);
  }
  .sticker {
    display: block;
    width: 1200px;
    height: 1200px;
  }
  .sticker-outline {
    fill: var(--sticker-white);
    stroke: var(--navy);
    stroke-width: 13;
    filter: drop-shadow(0 6px 10px rgba(0, 0, 0, 0.18));
  }
  .headline {
    font-family: "Ubuntu", sans-serif;
    font-weight: 500;
    font-size: 150px;
    letter-spacing: -4px;
  }
  .headline-still { fill: var(--ink-dark); }
  .headline-have { fill: var(--navy-bright); }
  .band-word {
    font-family: "Ubuntu", sans-serif;
    font-weight: 500;
    font-size: 128px;
    letter-spacing: -2px;
    fill: var(--sticker-white);
  }
  .call-line {
    font-family: "Gabriela", serif;
    font-size: 42px;
    fill: var(--ink-script);
  }
  .free-line {
    font-family: "Merienda", cursive;
    font-weight: 700;
    font-size: 104px;
    letter-spacing: -4px;
    fill: var(--navy-bright);
  }
</style>
</head>
<body>
<svg class="sticker" viewBox="0 0 1200 1200" xmlns="http://www.w3.org/2000/svg">
  <defs>
    <clipPath id="sticker-inner">
      <path d="M600,110 A410,410 0 0 1 1010,520 C1010,700 895,846 600,1074 C305,846 190,700 190,520 A410,410 0 0 1 600,110 Z"/>
    </clipPath>
    <linearGradient id="band-fill" x1="0" y1="0" x2="1" y2="0">
      <stop offset="0" stop-color="#1a2368"/>
      <stop offset="0.5" stop-color="#1f2c86"/>
      <stop offset="1" stop-color="#1a2368"/>
    </linearGradient>
    <radialGradient id="gloss-fill" cx="0.7" cy="0.35" r="0.7">
      <stop offset="0.6" stop-color="#ffffff"/>
      <stop offset="1" stop-color="#e6e6e6"/>
    </radialGradient>
  </defs>

  <path class="sticker-outline" d="M600,104 A416,416 0 0 1 1017,520 C1017,702 900,850 600,1082 C300,850 183,702 183,520 A416,416 0 0 1 600,104 Z"/>

  <g clip-path="url(#sticker-inner)">
    <rect class="sticker-gloss" x="190" y="110" width="820" height="970" fill="var(--gloss-grey)"/>
    <circle cx="760" cy="700" r="480" fill="url(#gloss-fill)"/>
    <rect class="question-band" x="180" y="517" width="840" height="138" fill="url(#band-fill)"/>
  </g>

  <text class="headline" x="604" y="429" text-anchor="middle">
    <tspan class="headline-still">Still </tspan><tspan class="headline-have">have</tspan>
  </text>
  <text class="band-word" x="598" y="614" text-anchor="middle">Questions?</text>
  <text class="call-line" x="615" y="720" text-anchor="middle">Call and request our book</text>
  <text class="free-line" x="600" y="845" text-anchor="middle">for free!</text>
</svg>
</body>
</html>
```